Bluefern Business Services needs a new interactive and interesting website

We need an interesting, professional, modern and functional company website for Bluefern Business Services - a young IT Services company based out of Chennai, India.

Bluefern Business Services is a fully owned subsidiary of Marlow Goods, one of the world's leading direct to consumer wine merchant.

We already have a registered company logo which must feature in the website.

We conceive, design, develop, test, implement and support IT solutions across the entire Marlow Goods IT landscape. For ex : We currently run about 25 e-commerce websites for Marlow Goods on ATG and Dot Net.

We would like to see our corporate colors used in the website. (Burgundy wine and wine green - source: www.bluefernbs-site.com)

We are looking at this website to communicate a fun, friendly and professionally managed company - reaching out to career seekers, prospective customers and general public.

For reference - The company name 'Bluefern' is an inspiration from the Marlow Goods lineage.

The second image with the world map is stickered on our main entrance to the office, I am not sure where this can be used -just putting it out there..

Please note that there are only a few more days to submit designs for this contest  !

I would appreciate if you can help posting your designs in time for our review and consideration.

Thanks.

Reason: Thanks for your inputs. We have a number of designers and a lot to digest and work with in the past few days. There has been a rush of new designs in the last few days Hence we will require more time to process these and make our decision. Hence i am requesting the contest to be open for more days. Regards, Tarun

Target Market(s)

Prospective job seekers who want to know more about the company and also wish to apply for a job vacancy
People wanting to know more about the company in general and our progress
People who want to see what we offer and how we can help them too - prospective customers
Companies that are interested in our IT Captive journey and are looking for a business opportunity

Industry/Entity Type

E-Commerce

Requirements
Must have
• Log In/ Register facility acting as a Single Sign on for Intranet (Employees)

Facility to post job vacancies (with an expiry date) and enable people to apply for a role and upload their CV/Resume.

Facility to Review Job applications

Facility for website visitors to contact Bluefern business Services via an online 'Contact Us' form with a split of job seekers and business opportunities

Gallery facility to upload pictures regarding company events
Nice to have
• Less Cluttered and contemporary design
Some Wine/Vineyard inspirations will be good but not too much, the company is an IT services company

```html
<!DOCTYPE html>
<html lang="en">
<head>
<meta charset="utf-8">
<title>Bluefern Business Services</title>
<link href="https://fonts.googleapis.com/css2?family=Ubuntu:wght@400;500&display=swap" rel="stylesheet">
<style>
:root{
  --burgundy:#8a0041;
  --burgundy-dark:#6d0033;
  --olive:#6f7a22;
  --olive-dark:#55601a;
  --ink:#333;
  --heading:#2f3316;
  --muted:#5a5a5a;
  --page:#f4f4f4;
  --footer:#2b2b2b;
  --field:#ebebeb;
}
*{margin:0;padding:0;box-sizing:border-box}
html,body{width:1025px;height:1200px;overflow:hidden}
body{position:relative;background:var(--page);font-family:'Ubuntu',sans-serif;color:var(--ink)}
.abs{position:absolute}

.site-header{left:0;top:0;width:1025px;height:122px;background:var(--burgundy);border-top:4px solid #3d0820}
.header-edge{left:0;top:116px;width:1025px;height:8px;
  background:linear-gradient(135deg,var(--burgundy) 50%,transparent 50%) 0 0/8px 8px,
             linear-gradient(225deg,var(--burgundy) 50%,transparent 50%) 0 0/8px 8px;z-index:2}
.brand{left:102px;top:20px;display:flex;align-items:center;gap:8px;color:#fff}
.brand-dot{width:24px;height:24px;border-radius:50%;background:#fff}
.brand-name{font-size:33px;font-weight:500;line-height:1;letter-spacing:-.5px}
.brand-sub{font-size:19px;font-weight:500;line-height:1.15;padding-left:2px}
.social{left:792px;top:39px;display:flex;gap:7px}
.social span{width:21px;height:21px;background:#fff;opacity:.85;border-radius:2px}

.hero{left:0;top:122px;width:1025px;height:382px;
  background:linear-gradient(90deg,#f1efeb 0%,#ece8e2 40%,#c9bfb3 60%,#8d7a6a 72%,#b8ada3 85%,#e6e3df 100%)}
.main-nav{left:100px;top:95px;width:834px;height:44px;z-index:3;
  background:linear-gradient(#7c872b,var(--olive-dark));display:flex;align-items:center}
.main-nav a{position:absolute;color:#fff;font-size:12.5px;text-decoration:none}
.main-nav a.active{left:14px;top:10px;width:53px;height:23px;background:#fff;color:var(--heading);
  font-weight:500;display:flex;align-items:center;justify-content:center;border-radius:2px}
.search{position:absolute;left:594px;top:9px;width:231px;height:23px;background:#fff;border-radius:2px;
  font-size:11px;color:#999;padding:5px 8px}
.search svg{position:absolute;right:6px;top:4px}

.hero-title{left:104px;top:233px;font-size:26px;color:var(--heading)}
.hero-text{left:106px;top:276px;width:350px;font-size:13px;line-height:17px;color:#555}
.hero-btn{left:106px;top:379px;width:146px;height:36px;background:#d4d4d4;color:#444;font-size:15.5px;
  display:flex;align-items:center;padding-left:13px;
  clip-path:polygon(0 0,85% 0,100% 50%,85% 100%,0 100%)}

.services{left:94px;top:504px;width:837px;height:323px;background:#fff;box-shadow:0 2px 6px rgba(0,0,0,.12)}
.service{position:absolute;top:14px;width:259px;text-align:center}
.service-img{height:131px;border:7px solid #e3e1dc}
.service h3{margin-top:21px;font-size:13.5px;font-weight:400;color:var(--burgundy)}
.service p{margin:14px auto 0;width:212px;font-size:11.5px;line-height:17px;color:var(--muted)}
.service .btn{display:inline-block;margin-top:11px;width:126px;height:24px;line-height:24px;background:var(--burgundy);color:#fff;font-size:12px}

.gallery-title{left:104px;top:864px;font-size:21px;color:#333}
.upload{left:505px;top:870px;font-size:12.5px;color:#333;text-decoration:underline}
.gallery-item{width:220px;height:109px;box-shadow:0 8px 8px -4px rgba(0,0,0,.35)}

.register{left:682px;top:899px;width:249px;height:235px;background:#fff;border:1px solid #ddd;padding:0 6px}
.register h2{margin:7px 0 9px 5px;font-size:17.5px;font-weight:400;color:#333}
.register .field{height:30px;background:var(--field);border:1px solid #d6d6d6;border-radius:2px;margin-bottom:7px;font-size:11px;color:#666;padding:9px 10px}
.register .submit{margin-top:9px;width:118px;height:32px;background:var(--olive-dark);color:#fff;font-size:13px;display:flex;align-items:center;justify-content:center}

.site-footer{left:0;top:1160px;width:1025px;height:40px;background:var(--footer);color:#fff;font-size:11.5px;display:flex;align-items:center;justify-content:center}
</style>
</head>
<body>
<header class="site-header abs">
  <div class="brand abs">
    <span class="brand-dot"></span>
    <div><div class="brand-name">bluefern</div><div class="brand-sub">Business Services</div></div>
  </div>
  <div class="social abs" aria-label="Social links"><span></span><span></span><span></span><span></span><span></span></div>
</header>
<div class="header-edge abs"></div>

<section class="hero abs" role="img" aria-label="Photo of a smiling man with a glass of red wine at a laptop in a bright kitchen"></section>
<nav class="main-nav abs">
  <a class="active" href="#">HOME</a>
  <a href="#" style="left:90px">About Us</a>
  <a href="#" style="left:174px">Clients</a>
  <a href="#" style="left:244px">Services</a>
  <a href="#" style="left:323px">Careers</a>
  <a href="#" style="left:398px">Contact Us</a>
  <div class="search">Search
    <svg width="14" height="14" viewBox="0 0 14 14"><circle cx="6" cy="6" r="4.5" fill="none" stroke="#6f7a22" stroke-width="2"/><line x1="9.5" y1="9.5" x2="13" y2="13" stroke="#6f7a22" stroke-width="2"/></svg>
  </div>
</nav>
<h1 class="hero-title abs" style="font-weight:400">Delivering IT Excellence</h1>
<p class="hero-text abs">Welcome to Bluefern Business Services, an emerging provider of global IT consulting and software services. We are part of the Marlow Goods group, a family run business and the world's largest multi-channel home delivery wine merchant.</p>
<div class="hero-btn abs">LEARN MORE</div>

<section class="services abs">
  <div class="service" style="left:16px">
    <div class="service-img" role="img" aria-label="Photo of a university application form with a pen" style="background:linear-gradient(160deg,#2a6fb8,#5a9ad6 45%,#e9e9ee 70%,#d8d8dd)"></div>
    <h3>Packaged Applications</h3>
    <p>It is a long established fact that a reader will be distracted by the readable content of a page when looking at its layout.</p>
    <span class="btn">Learn More</span>
  </div>
  <div class="service" style="left:290px">
    <div class="service-img" role="img" aria-label="Diagram of cloud solutions and enterprise services" style="background:radial-gradient(circle at 62% 50%,#fff 12%,#c9ccd0 30%,#7d8791 46%,#f3f3f3 48%)"></div>
    <h3>Enterprise Application Integration</h3>
    <p>It is a long established fact that a reader will be distracted by the readable content of a page when looking at its layout.</p>
    <span class="btn">Learn More</span>
  </div>
  <div class="service" style="left:563px">
    <div class="service-img" role="img" aria-label="Photo of a metallic jigsaw globe on a map" style="background:linear-gradient(135deg,#2c3d6a,#9fb0cf 45%,#5b6d97 70%,#d9c27a)"></div>
    <h3>Application Development &amp; Maintenance</h3>
    <p>It is a long established fact that a reader will be distracted by the readable content of a page when looking at its layout.</p>
    <span class="btn">Learn More</span>
  </div>
</section>

<h2 class="gallery-title abs" style="font-weight:400">Gallery</h2>
<a class="upload abs" href="#">Upload Picture</a>
<div class="gallery-item abs" style="left:101px;top:899px;background:linear-gradient(135deg,#6fa3d8,#b8cfe6 45%,#1f2b4a 75%)" role="img" aria-label="Photo of a businesswoman typing on a laptop"></div>
<div class="gallery-item abs" style="left:377px;top:899px;background:linear-gradient(90deg,#1c1c1c,#4a4a4a 35%,#d9dde0 65%,#f1f1f1)" role="img" aria-label="Photo of a man working at a computer monitor"></div>
<div class="gallery-item abs" style="left:101px;top:1025px;background:linear-gradient(90deg,#2a1e16,#6b5038 40%,#3a3030 70%,#aeb1b4)" role="img" aria-label="Photo of a man on the phone at a laptop"></div>
<div class="gallery-item abs" style="left:377px;top:1025px;background:linear-gradient(90deg,#c45a2a,#3a5fa8 35%,#8bbf4a 70%,#d7d2c6)" role="img" aria-label="Photo of an office with colourful chairs"></div>

<form class="register abs">
  <h2>Register Here</h2>
  <div class="field">First Name</div>
  <div class="field">Last Name</div>
  <div class="field">Contact Number</div>
  <div class="field">Email</div>
  <div class="submit">Register Now!</div>
</form>

<footer class="site-footer abs">Copyright Bluefern Business Services Private Limited.</footer>
</body>
</html>
```